Sale PPC Banner Ad Design Update

We need some Google PPC Banner Ad's for our sale altered to include product shots in the background. Attached are some examples that we currently use. We want a similar format/look but with the attached product shots used as the background image. Product image is called "KTPOle Grade 4"

Have also included our logo file as well.

Industry/Entity Type

Google

Font styles to use
Sans Serif

Requirements
Must have
• The must-have sizes (up to 150kb):
• • Banner: 468 x 60
• • Large mobile banner 320 x 100
• • Leaderboard: 728 x 90
• • Square: 250 x 250
• • Small square: 200 x 200
• • Large rectangle: 336 x 280
Nice to have
• The nice-to-have sizes:
• • Vertical rectangle: 240 x 400
• • Mobile leaderboard: 320 x 50
• • Inline rectangle: 300 x 250
• • Skyscraper: 120 x 600
• • Wide skyscraper: 160 x 600
• • Half-page: 300 x 600
• • Large leaderboard: 970 x 90
• • Billboard: 970 x 250
• • Portrait: 300 x 1050

```html
<!DOCTYPE html>
<html lang="en">
<head>
<meta charset="UTF-8">
<title>Luxury Shoes Sale Banner</title>
<link rel="stylesheet" href="https://fonts.googleapis.com/css2?family=Open+Sans:wght@300;400;600&display=swap">
<style>
  :root {
    --paper: #ffffff;
    --ink: #111111;
    --sale-red: #f2434f;
    --headline: #f1f1f1;
    --photo-dark: #1b1a22;
    --photo-navy: #28304f;
    --photo-red: #8a1f33;
    --photo-gold: #8a7a2a;
  }
  * { margin: 0; padding: 0; box-sizing: border-box; }
  html, body {
    width: 1200px;
    height: 309px;
    overflow: hidden;
    background: var(--paper);
  }
  .banner {
    position: relative;
    width: 1200px;
    height: 309px;
    display: flex;
    font-family: "Open Sans", Arial, sans-serif;
  }
  .brand-strip {
    width: 114px;
    height: 100%;
    background: var(--paper);
    display: flex;
    align-items: center;
    justify-content: center;
  }
  .brand-name {
    transform: rotate(-90deg);
    white-space: nowrap;
    font-size: 62px;
    font-weight: 400;
    color: var(--ink);
    letter-spacing: 0;
  }
  .product-scene {
    position: relative;
    flex: 1;
    height: 100%;
    overflow: hidden;
  }
  .product-photo {
    position: absolute;
    inset: 0;
    width: 100%;
    height: 100%;
    display: block;
  }
  .sale-copy {
    position: absolute;
    left: 0;
    top: 0;
    width: 964px;
    height: 100%;
    text-align: center;
    color: var(--headline);
  }
  .sale-copy .kicker {
    position: absolute;
    left: 0;
    right: 0;
    top: 40px;
    font-size: 37px;
    font-weight: 400;
    letter-spacing: 5px;
  }
  .sale-copy .sale-word {
    position: absolute;
    left: 0;
    right: 0;
    top: 78px;
    font-size: 118px;
    line-height: 1.15;
    font-weight: 300;
    letter-spacing: 18px;
    color: var(--sale-red);
  }
  .sale-copy .cta {
    position: absolute;
    left: 0;
    right: 0;
    top: 222px;
    font-size: 37px;
    font-weight: 400;
    letter-spacing: 5px;
  }
</style>
</head>
<body>
  <div class="banner">
    <aside class="brand-strip">
      <span class="brand-name">Kt.Pole</span>
    </aside>
    <section class="product-scene">
      <svg class="product-photo" viewBox="0 0 1086 309" preserveAspectRatio="none" role="img" aria-label="Two pairs of black and white penny loafers worn with blue patterned trousers, standing on a colourful red, yellow and blue geometric rug, darkened behind the text">
        <defs>
          <linearGradient id="rug-tones" x1="0" y1="0" x2="1" y2="1">
            <stop offset="0" stop-color="var(--photo-navy)"/>
            <stop offset="0.35" stop-color="var(--photo-red)"/>
            <stop offset="0.65" stop-color="var(--photo-gold)"/>
            <stop offset="1" stop-color="var(--photo-red)"/>
          </linearGradient>
          <radialGradient id="shade" cx="0.44" cy="0.5" r="0.6">
            <stop offset="0" stop-color="var(--photo-dark)" stop-opacity="0.75"/>
            <stop offset="1" stop-color="var(--photo-dark)" stop-opacity="0.45"/>
          </radialGradient>
        </defs>
        <rect width="1086" height="309" fill="url(#rug-tones)"/>
        <rect width="1086" height="309" fill="url(#shade)"/>
      </svg>
      <div class="sale-copy">
        <p class="kicker">LUXURY SHOES</p>
        <p class="sale-word">SALE</p>
        <p class="cta">SHOP NOW</p>
      </div>
    </section>
  </div>
</body>
</html>
```